Tavel Website

Need a 4 page Drupal website - Home, About Us, Portfolio, Contact for a private equity/venture capital firm and new logo - company name is Tavel Corporation. The design should communicate - stock markets, hedge funds, deal-making, investments. The Portfolio section is to showcase the small companies we invest in. Hoping for something fresh, dynamic, even fun - no cliche financial images of New York. Not technical - but know how use Drupal content management to make text edits, blocks, articles, etc. We don't use any social media - so no chirply, Pagebook or WorkNode links. We need space for a post heron email sign-up form. Need website uploaded to my Corvane web hosting account. First time user of Sketch Plaza - have 3 other company websites that need refreshing.

```html
<!DOCTYPE html>
<html lang="en">
<head>
<meta charset="utf-8">
<title>Tavel Corporation – Equity &amp; Venture Capital</title>
<link href="https://fonts.googleapis.com/css2?family=Oswald:wght@400;500&family=Open+Sans:wght@400;600&display=swap" rel="stylesheet">
<style>
:root{
  --accent:#3bb3d8;
  --accent-dark:#2a9cc2;
  --ink:#222222;
  --text:#8a8a8a;
  --line:#e6e6e6;
  --dark:#1c1f22;
  --footer:#242424;
  --footer-field:#2c2c2c;
  --footer-text:#8c8c8c;
  --white:#ffffff;
}
*{box-sizing:border-box;margin:0;padding:0}
html,body{width:1200px;height:2177px;overflow:hidden}
body{position:relative;background:var(--white);font-family:"Open Sans",Arial,sans-serif;color:var(--text)}
.abs{position:absolute}

/* header */
.site-header{position:absolute;left:0;top:0;width:1200px;height:110px;background:var(--white)}
.brand{position:absolute;left:171px;top:30px;display:flex;align-items:center;gap:14px}
.brand-mark{width:40px;height:40px;background:var(--accent)}
.brand-name{font-family:"Oswald",sans-serif;font-weight:400;font-size:30px;color:var(--accent);letter-spacing:.3px}
.main-nav{position:absolute;top:39px;left:691px;display:flex;gap:22px}
.main-nav a{font-size:15px;color:#555;text-decoration:none;height:34px;line-height:34px;padding:0 12px;border-radius:3px}
.main-nav a.active{background:var(--accent);color:var(--white)}

/* hero */
.hero{position:absolute;left:0;top:110px;width:1200px;height:488px;
  background:linear-gradient(160deg,#6f9cc7 0%,#4c7fb3 35%,#a9c4de 65%,#dfe6ee 100%)}
.hero-tag{position:absolute;left:173px;top:193px;height:39px;padding:0 18px;background:var(--accent);color:var(--white);
  font-family:"Oswald",sans-serif;font-size:22px;line-height:39px}
.hero-title{position:absolute;left:173px;top:234px;height:72px;padding:0 18px;background:#232323;color:var(--white);
  font-family:"Oswald",sans-serif;font-weight:500;font-size:46px;line-height:72px}
.hero-arrow{position:absolute;top:237px;width:34px;height:34px;border-radius:50%;background:#222;display:flex;align-items:center;justify-content:center}
.hero-arrow.prev{left:53px}.hero-arrow.next{left:1116px}

/* welcome */
.welcome-title{position:absolute;left:0;top:628px;width:1200px;text-align:center;font-family:"Oswald",sans-serif;font-size:36px;color:var(--ink)}
.welcome-title span{color:var(--accent)}
.welcome-sub{position:absolute;left:0;top:681px;width:1200px;text-align:center;font-size:16px;color:#999}
.intro{position:absolute;left:177px;top:725px;width:846px;text-align:center;font-size:11.5px;line-height:20px;color:#999}

.services{position:absolute;left:171px;top:795px;width:859px;height:292px}
.services .v-rule{position:absolute;left:428px;top:0;width:1px;height:292px;background:var(--line)}
.services .h-rule{position:absolute;left:0;top:148px;width:859px;height:1px;background:var(--line)}
.service{position:absolute;width:400px}
.service .icon{position:absolute;left:0;top:0;width:100px;height:100px;border-radius:50%;border:1px solid #eef2f4;display:flex;align-items:center;justify-content:center}
.service h3{position:absolute;left:124px;top:18px;font-weight:400;font-size:19px;color:var(--accent)}
.service p{position:absolute;left:124px;top:55px;width:276px;font-size:11.5px;line-height:19.5px;text-align:justify;color:#999}
.s1{left:0;top:22px}.s2{left:460px;top:22px}.s3{left:0;top:176px}.s4{left:460px;top:176px}

/* about */
.about{position:absolute;left:0;top:1125px;width:1200px;height:433px;background:linear-gradient(180deg,#232830,#161a1f)}
.section-title{position:absolute;left:0;width:1200px;text-align:center;font-family:"Oswald",sans-serif;font-weight:500;font-size:21px}
.section-title::after{content:"";display:block;width:40px;height:2px;margin:10px auto 0;background:currentColor;opacity:.8}
.about .section-title{top:38px;color:var(--white)}
.video{position:absolute;left:171px;top:123px;width:392px;height:258px;border:5px solid #3a3f45;
  background:linear-gradient(135deg,#1f4e88 0%,#3d7bc0 45%,#183a66 100%)}
.video .play{position:absolute;left:145px;top:80px;width:88px;height:88px;border-radius:50%;border:6px solid rgba(255,255,255,.85);display:flex;align-items:center;justify-content:center}
.video .bar{position:absolute;left:16px;right:16px;bottom:8px;height:6px;background:#555}
.video .bar i{display:block;width:45%;height:100%;background:var(--accent)}
.about-copy{position:absolute;left:591px;top:112px;width:440px}
.about-copy h2{font-family:"Oswald",sans-serif;font-weight:400;font-size:34px;color:var(--white)}
.about-copy h4{margin-top:6px;font-weight:400;font-size:16px;color:var(--accent)}
.about-copy p{margin-top:10px;font-size:12.5px;line-height:20.5px;color:#b4b8bc;text-align:justify}
.btn{display:inline-block;background:var(--accent);color:var(--white);text-decoration:none;border-radius:2px}
.about-copy .btn{margin-top:20px;height:38px;line-height:38px;padding:0 22px;font-size:15px}

/* portfolio */
.portfolio .section-title{top:1585px;color:var(--ink)}
.portfolio-intro{position:absolute;left:177px;top:1636px;width:846px;text-align:center;font-size:11.5px;line-height:20px;color:#999}
.partner-row{position:absolute;left:170px;top:1716px;width:860px;height:44px;display:flex;align-items:center;justify-content:space-between}
.partner{font-family:"Open Sans",sans-serif;font-weight:600;font-size:21px;color:#1e4f8f;white-space:nowrap}
.carousel-btn{position:absolute;top:1729px;width:20px;height:20px;border-radius:50%;border:1px solid #ddd;display:flex;align-items:center;justify-content:center}

/* footer */
.site-footer{position:absolute;left:0;top:1799px;width:1200px;height:378px;background:var(--footer)}
.footer-heading{position:absolute;top:34px;font-size:15px;color:var(--footer-text);text-transform:uppercase}
.field{position:absolute;background:var(--footer-field);border:1px solid #3d3d3d;font-size:10.5px;color:#777;padding:8px}
.signup-btn{position:absolute;left:171px;top:228px;width:177px;height:31px;line-height:31px;text-align:center;font-size:12px;background:var(--accent-dark)}
.note{position:absolute;left:171px;top:271px;font-size:10px;color:#777}
.map{position:absolute;left:530px;top:74px;width:499px;height:208px;background:linear-gradient(135deg,#e8e0c8,#d6dfc8 50%,#e9e2cf)}
.copyright{position:absolute;left:171px;top:335px;font-size:10.5px;color:#666}
.back-top{position:absolute;left:975px;top:336px;font-size:10.5px;color:#9aa84a;text-decoration:none}
</style>
</head>
<body>

<header class="site-header">
  <div class="brand"><span class="brand-mark"></span><span class="brand-name">TAVEL CORPORATION</span></div>
  <nav class="main-nav">
    <a href="#" class="active">Home</a><a href="#">About Us</a><a href="#">Portfolio</a><a href="#">Contact Us</a>
  </nav>
</header>

<section class="hero" role="img" aria-label="Photo of a hand with a pen over a blue stock market chart on a screen">
  <div class="hero-tag">TAVEL CORPORATION</div>
  <div class="hero-title">STOCK MARKETS</div>
  <span class="hero-arrow prev"><svg width="12" height="12" viewBox="0 0 12 12"><path d="M8 1 3 6l5 5" fill="none" stroke="#fff" stroke-width="2"/></svg></span>
  <span class="hero-arrow next"><svg width="12" height="12" viewBox="0 0 12 12"><path d="M4 1l5 5-5 5" fill="none" stroke="#fff" stroke-width="2"/></svg></span>
</section>

<h1 class="welcome-title">Welcome to <span>Tavel Corporation</span></h1>
<p class="welcome-sub">Equity &amp; Venture capital</p>
<p class="intro">Duis aute irure dolor in reprehenderit in voluptate velit esse cillum dolore eu fugiat nulla pariatur. Excepteur sint occaecat cupidatat non proident, sunt in culpa qui officia deserunt mollit anim id est laborum. Ut enim minim veniam, quis nostrud exercitation ullamco labor</p>

<section class="services">
  <span class="v-rule"></span><span class="h-rule"></span>
  <div class="service s1">
    <div class="icon"><svg width="46" height="40" viewBox="0 0 46 40"><rect x="2" y="2" width="42" height="28" fill="none" stroke="#3bb3d8" stroke-width="3"/><path d="M9 24l8-8 6 5 10-11" fill="none" stroke="#3bb3d8" stroke-width="2.5"/><rect x="10" y="20" width="4" height="6" fill="#3bb3d8"/><rect x="18" y="18" width="4" height="8" fill="#3bb3d8"/><rect x="26" y="16" width="4" height="10" fill="#3bb3d8"/><path d="M17 38h12M23 30v8" stroke="#3bb3d8" stroke-width="3"/></svg></div>
    <h3>Stock Markets</h3>
    <p>There are many variations of passages of Lorem Ipsum, but the majority have suffered alteration. There are many variations of passages of Lorem</p>
  </div>
  <div class="service s2">
    <div class="icon"><svg width="48" height="44" viewBox="0 0 48 44"><circle cx="26" cy="10" r="8" fill="none" stroke="#3bb3d8" stroke-width="2"/><text x="26" y="14" font-size="11" text-anchor="middle" fill="#3bb3d8" font-family="Open Sans, sans-serif">$</text><ellipse cx="24" cy="30" rx="17" ry="11" fill="none" stroke="#3bb3d8" stroke-width="2.5"/><path d="M14 40v3M32 40v3M41 28h4" stroke="#3bb3d8" stroke-width="2.5"/></svg></div>
    <h3>Hedge Funds</h3>
    <p>There are many variations of passages of Lorem Ipsum, but the majority have suffered alteration. There are many variations of passages of Lorem</p>
  </div>
  <div class="service s3">
    <div class="icon"><svg width="50" height="48" viewBox="0 0 50 48"><rect x="4" y="34" width="7" height="12" fill="#3bb3d8"/><rect x="14" y="28" width="7" height="18" fill="#3bb3d8"/><rect x="24" y="22" width="7" height="24" fill="#3bb3d8"/><rect x="34" y="16" width="7" height="30" fill="#3bb3d8"/><path d="M4 26 30 6" stroke="#3bb3d8" stroke-width="4"/><path d="M24 3h12v12z" fill="#3bb3d8"/></svg></div>
    <h3>Deal Making</h3>
    <p>There are many variations of passages of Lorem Ipsum, but the majority have suffered alteration. There are many variations of passages of Lorem</p>
  </div>
  <div class="service s4">
    <div class="icon"><svg width="40" height="54" viewBox="0 0 40 54"><text x="20" y="46" font-size="54" font-weight="600" text-anchor="middle" fill="#3bb3d8" font-family="Open Sans, sans-serif">$</text></svg></div>
    <h3>Investments</h3>
    <p>There are many variations of passages of Lorem Ipsum, but the majority have suffered alteration. There are many variations of passages of Lorem</p>
  </div>
</section>

<section class="about">
  <h2 class="section-title">ABOUT US</h2>
  <div class="video" role="img" aria-label="Video still of a businessman touching a rising chart on a glass screen">
    <span class="play"><svg width="30" height="34" viewBox="0 0 30 34"><path d="M4 2l24 15L4 32z" fill="rgba(255,255,255,.85)"/></svg></span>
    <span class="bar"><i></i></span>
  </div>
  <div class="about-copy">
    <h2>Equity &amp; Venture capital</h2>
    <h4>Sed ut perspiciatis unde omnis iste</h4>
    <p>Lorem ipsum dolor sit amet, consectetur adipiscing elit, sed do eiusmod tempor incididunt ut labore et dolore magna aliqua. Ut enim ad minim veniam, quis nostrud exercitation ullamco laboris nisi ut aliquip ex ea commodo consequat. Duis aute irure dolor in reprehenderit in voluptate velit esse cillum dolore eu fugiat nulla pariatur. Excepteur sint occaecat cupidatat non proident, sunt in culpa qui officia deserunt mollit anim id est laborum.</p>
    <a href="#" class="btn">Watch the video</a>
  </div>
</section>

<section class="portfolio">
  <h2 class="section-title">OUR PORTFOLIO</h2>
  <p class="portfolio-intro">Duis aute irure dolor in reprehenderit in voluptate velit esse cillum dolore eu fugiat nulla pariatur. Excepteur sint occaecat cupidatat non proident, sunt in culpa qui officia deserunt mollit anim id est laborum. Ut enim minim veniam, quis nostrud exercitation ullamco labor</p>
  <span class="carousel-btn" style="left:122px"><svg width="6" height="8" viewBox="0 0 6 8"><path d="M5 0 1 4l4 4" fill="none" stroke="#999"/></svg></span>
  <div class="partner-row">
    <span class="partner">Renalith</span>
    <span class="partner">Vistachip</span>
    <span class="partner">Netcoda</span>
    <span class="partner">Corvale Ltd.</span>
    <span class="partner">Meres Leisure</span>
    <span class="partner">Isleway</span>
  </div>
  <span class="carousel-btn" style="left:1056px"><svg width="6" height="8" viewBox="0 0 6 8"><path d="M1 0l4 4-4 4" fill="none" stroke="#999"/></svg></span>
</section>

<footer class="site-footer">
  <h3 class="footer-heading" style="left:171px;font-weight:400">Newsletter Signup</h3>
  <div class="field" style="left:171px;top:76px;width:151px;height:31px">Your name</div>
  <div class="field" style="left:334px;top:76px;width:151px;height:31px">Email address</div>
  <div class="field" style="left:171px;top:119px;width:314px;height:96px">Message</div>
  <a href="#" class="btn signup-btn">NEWSLETTER SIGNUP</a>
  <p class="note">Make sure you put a valid email.</p>

  <h3 class="footer-heading" style="left:528px;font-weight:400">Our Location</h3>
  <div class="map" role="img" aria-label="Street map showing the office location"></div>

  <p class="copyright">© 2013 Tavel Corporation. All rights reserved.</p>
  <a href="#" class="back-top">Back to top</a>
</footer>

</body>
</html>
```